Business Landing Page for SEO Company

Need the landing page of the website designed - I will provide the copy, will need to include details of my company and the services offered, about us, testimonials, faq, etc., and all these elements will need to be arranged graphically on the page.

I want something similar to this: https://torvanequill.com/

Not in terms of color or theme or anything, but we offer a similar service and want to display similar information.

Th services we provide are:

Premium Links
Monthly Links Subscription
Link Insertions

Need to advertise them on the front page. Additionally need a place for testimonials, company details, etc.,

We already have logo for the website. Please use the attached file to insert the logo within the overal design.

Target Market(s)

SEO marketers and agencies

Number of Pages Required

1 page

```html
<!DOCTYPE html>
<html lang="en">
<head>
<meta charset="utf-8">
<title>Northpeak – Link Building Service</title>
<link href="https://fonts.googleapis.com/css2?family=Montserrat:wght@400;500;600;700;800&family=Open+Sans:wght@400;600&display=swap" rel="stylesheet">
<style>
:root{
  --blue:#2a7de1;
  --blue-dark:#1b64b3;
  --faq:#1d6cb5;
  --orange:#f57c00;
  --ink:#1c1c1c;
  --text:#555;
  --muted:#8a8f98;
  --dark:#111214;
  --card-dark:#1b1c1f;
  --sky:#e7f1fb;
  --white:#fff;
}
*{box-sizing:border-box;margin:0;padding:0}
html,body{width:1200px;height:3740px;overflow:hidden}
body{font-family:"Open Sans",Arial,sans-serif;color:var(--text);background:var(--white);position:relative}
h1,h2,h3,h4,.brand,.btn,.nav{font-family:"Montserrat",Arial,sans-serif}
.btn{display:inline-block;font-size:12px;font-weight:600;padding:10px 22px;border-radius:3px;color:var(--white);background:var(--blue)}
.rule{width:40px;height:2px;background:var(--blue);margin:12px auto}

/* header */
.site-header{position:absolute;top:0;left:0;width:1200px;height:50px;background:var(--white);display:flex;align-items:center;padding:0 150px;justify-content:space-between}
.brand{font-size:20px;font-weight:600;color:var(--ink);letter-spacing:.5px}
.nav{display:flex;gap:28px;align-items:center;font-size:12px;color:var(--ink);font-weight:500}
.nav .active{color:var(--blue)}

/* hero */
.hero{position:absolute;top:50px;left:0;width:1200px;height:690px;background:radial-gradient(ellipse at 50% 30%,#2a2c31 0%,#141517 60%,#0b0b0c 100%);overflow:hidden}
.hero-map{position:absolute;left:80px;top:10px;width:1040px;height:430px;background:radial-gradient(ellipse at center,rgba(255,255,255,.08),rgba(255,255,255,0) 70%)}
.hero-kicker{position:absolute;top:150px;width:100%;text-align:center;color:var(--white);font-size:20px;font-weight:700;letter-spacing:1px}
.hero-title{position:absolute;top:180px;width:100%;text-align:center;color:var(--white);font-size:50px;font-weight:800;letter-spacing:2px}
.hero-copy{position:absolute;top:258px;left:290px;width:620px;text-align:center;color:#d8d8d8;font-size:13px;line-height:1.6}
.hero-wave{position:absolute;left:0;bottom:0}

.services{position:absolute;top:490px;left:150px;width:900px;display:flex;gap:50px}
.service{width:266px;height:385px;background:var(--card-dark);border:1px solid #333;border-radius:4px;text-align:center;padding:42px 20px 0;position:relative;box-shadow:0 10px 30px rgba(0,0,0,.25)}
.service.featured{background:#151517;border-color:#444}
.service h3{color:var(--white);font-size:14px;font-weight:700;margin-top:26px;white-space:nowrap}
.service .rule{background:var(--orange)}
.service p{color:#c4c4c4;font-size:12px;line-height:1.6}
.service .btn{position:absolute;bottom:26px;left:28px;right:28px;padding:11px 0;background:var(--white);color:var(--ink)}
.service.featured .btn{background:var(--orange);color:var(--white)}

/* about */
.about{position:absolute;top:960px;left:150px;width:900px;height:320px}
.about h2{font-size:34px;font-weight:700;color:var(--ink)}
.about .rule{margin:12px 0 18px}
.about p{width:440px;font-size:12.5px;line-height:1.65;margin-bottom:12px}
.about-art{position:absolute;right:0;top:-20px;width:360px;height:300px;border-radius:12px;background:linear-gradient(135deg,#eef3fd,#c9dbf7)}

/* testimonials */
.testimonials{position:absolute;top:1360px;left:0;width:1200px;height:600px;background:var(--sky)}
.section-title{text-align:center;font-size:28px;font-weight:700;color:var(--ink)}
.section-sub{text-align:center;font-size:11px;color:var(--muted)}
.quotes{position:absolute;top:210px;left:150px;width:900px;display:flex;gap:45px}
.quote{width:270px;height:210px;background:var(--white);border-radius:4px;text-align:center;padding:75px 24px 0;position:relative}
.quote.mid{margin-top:20px}
.avatar{position:absolute;top:-40px;left:95px;width:80px;height:80px;border-radius:50%;background:linear-gradient(135deg,#9aa3ad,#5b636d);border:4px solid var(--white)}
.quote p{font-size:11px;color:#b0b4ba;line-height:1.55}
.quote h4{font-size:14px;color:var(--ink);margin-top:14px}
.quote span{font-size:10px;color:var(--orange)}
.dots{position:absolute;top:512px;left:583px;display:flex;gap:8px}
.dots i{width:8px;height:8px;border-radius:50%;background:#f6b27a}
.dots i:first-child{background:var(--orange)}

/* faq */
.faq{position:absolute;top:2050px;left:0;width:1200px}
.faq-list{width:780px;margin:34px auto 0}
.faq-item{height:38px;background:var(--faq);color:var(--white);font-family:"Montserrat",Arial,sans-serif;font-size:14px;font-weight:500;display:flex;align-items:center;justify-content:center;position:relative;margin-bottom:12px}
.faq-item::after{content:"+";position:absolute;right:14px;font-size:18px}
.faq-item.open::after{content:"–"}
.faq-item.open{margin-bottom:0}
.faq-answer{background:#3a86c8;color:var(--white);font-size:13px;line-height:1.6;text-align:center;padding:22px 60px;margin-bottom:12px;height:120px}
.faq .btn{display:block;width:130px;margin:28px auto 0;text-align:center;background:var(--orange);padding:10px 0}

/* contact */
.contact{position:absolute;top:2730px;left:0;width:1200px;height:590px;background:var(--sky)}
.contact-card{position:absolute;top:90px;left:150px;width:900px;height:400px;background:var(--white);padding:40px 40px;display:flex}
.contact-card h2{font-size:26px;font-weight:700;color:var(--ink)}
.contact-card .rule{margin:10px 0 24px}
.form{width:410px}
.row{display:flex;gap:14px;margin-bottom:14px}
.field{flex:1;height:34px;background:#f1f2f4;border:1px solid #e3e5e8;font-size:10px;color:#a0a4aa;padding:10px}
.field.area{height:100px}
.form .btn{margin-top:10px;padding:8px 18px;background:var(--blue-dark)}
.info{margin-left:60px;padding-left:40px;border-left:1px solid #e5e5e5;margin-top:60px;height:260px}
.info-item{display:flex;gap:18px;margin-bottom:26px;align-items:flex-start}
.info-icon{width:38px;height:38px;border:1px solid #ddd;display:flex;align-items:center;justify-content:center}
.info h4{font-size:14px;color:var(--ink)}
.info p{font-size:11px;color:var(--text)}

/* footer */
.site-footer{position:absolute;top:3320px;left:0;width:1200px;height:420px;background:var(--dark);overflow:hidden;color:#cfcfcf}
.footer-mark{position:absolute;top:20px;left:0;width:100%;text-align:center;font-family:"Montserrat",Arial,sans-serif;font-size:150px;font-weight:600;color:#1b1c1f}
.footer-cols{position:absolute;top:75px;left:150px;width:900px;display:flex}
.footer-cols h4{font-size:14px;color:var(--white);margin-bottom:16px}
.col-about{width:330px}
.col-about p{font-size:11px;line-height:1.6;width:270px}
.col-about .call{margin-top:18px;font-size:11px}
.col-about .phone{font-size:17px;color:var(--orange);font-weight:700;font-family:"Montserrat",Arial,sans-serif}
.col-links{width:330px}
.links{display:grid;grid-template-columns:120px 120px;gap:8px;font-size:11px}
.links .current{color:var(--orange)}
.news .input{width:240px;height:30px;background:var(--white);font-size:10px;color:#999;padding:8px 10px;margin-bottom:12px}
.news .btn{background:var(--orange);padding:8px 16px}
.footer-bottom{position:absolute;top:365px;left:150px;width:900px;display:flex;justify-content:space-between;align-items:center;font-size:10px;color:#9a9a9a}
.socials{display:flex;gap:10px}
.socials i{width:22px;height:22px;background:#f0f0f0;border-radius:2px}
.socials i:first-child{background:var(--orange)}
</style>
</head>
<body>

<header class="site-header">
  <div class="brand">Northpeak</div>
  <nav class="nav">
    <span class="active">Services</span><span>About Us</span><span>Testimonials</span><span>Faq</span>
    <span class="btn">Contact Us</span>
  </nav>
</header>

<section class="hero">
  <div class="hero-map" role="img" aria-label="Dotted world map backdrop"></div>
  <div class="hero-kicker">THE LEADER OF THE MARKET</div>
  <h1 class="hero-title">BUILDING SERVICE</h1>
  <p class="hero-copy">Lorem ipsum dolor sit amet, consectetur adipiscing elit, sed do eiusmod tempor incididunt ut labore et dolore magna aliqua. Ut enim ad minim veniam, quis nostrud exercitation ullamco laboris nisi ut aliquip ex ea commodo consequat. Duis aute irure dolor in reprehenderit in voluptate velit esse cillum.</p>
  <svg class="hero-wave" width="1200" height="220" viewBox="0 0 1200 220">
    <path d="M0 150 Q600 20 1200 150 L1200 220 L0 220Z" fill="var(--orange)"/>
    <path d="M0 170 Q600 50 1200 170 L1200 220 L0 220Z" fill="#fff"/>
  </svg>
</section>

<div class="services">
  <div class="service">
    <svg width="34" height="34" viewBox="0 0 24 24" fill="none" stroke="var(--orange)" stroke-width="2.6" stroke-linecap="round"><path d="M10 14a4 4 0 0 0 5.7 0l3-3a4 4 0 0 0-5.7-5.7l-1 1"/><path d="M14 10a4 4 0 0 0-5.7 0l-3 3a4 4 0 0 0 5.7 5.7l1-1"/></svg>
    <h3>Premium Links</h3><div class="rule"></div>
    <p>Sed ut perspiciatis unde omnis iste natus error sit voluptatem accusantium doloremque laudantium totam rem aperiam.</p>
    <span class="btn">View Options</span>
  </div>
  <div class="service featured">
    <svg width="34" height="34" viewBox="0 0 24 24" fill="none" stroke="var(--orange)" stroke-width="2.6" stroke-linecap="round"><path d="M10 14a4 4 0 0 0 5.7 0l3-3a4 4 0 0 0-5.7-5.7l-1 1"/><path d="M14 10a4 4 0 0 0-5.7 0l-3 3a4 4 0 0 0 5.7 5.7l1-1"/></svg>
    <h3>Monthly Links Subscription</h3><div class="rule"></div>
    <p>Consectetur adipiscing elit, sed do eiusmod tempor incididunt ut labore et dolore magna aliqua enim minim.</p>
    <span class="btn">View Options</span>
  </div>
  <div class="service">
    <svg width="34" height="34" viewBox="0 0 24 24" fill="none" stroke="var(--orange)" stroke-width="2.6" stroke-linecap="round"><path d="M10 14a4 4 0 0 0 5.7 0l3-3a4 4 0 0 0-5.7-5.7l-1 1"/><path d="M14 10a4 4 0 0 0-5.7 0l-3 3a4 4 0 0 0 5.7 5.7l1-1"/></svg>
    <h3>Link Insertions</h3><div class="rule"></div>
    <p>Nemo enim ipsam voluptatem quia voluptas sit aspernatur aut odit aut fugit sed quia magni dolores.</p>
    <span class="btn">View Options</span>
  </div>
</div>

<section class="about">
  <h2>About Us</h2><div class="rule"></div>
  <p>Lorem ipsum dolor sit amet, consectetur adipiscing elit, sed do eiusmod tempor incididunt ut labore et dolore magna aliqua. Ut enim ad minim veniam, quis nostrud exercitation ullamco laboris nisi ut aliquip ex ea commodo consequat. Duis aute irure dolor in reprehenderit in voluptate velit esse cillum dolore eu fugiat nulla pariatur.</p>
  <p>Excepteur sint occaecat cupidatat non proident, sunt in culpa qui officia deserunt mollit anim id est laborum sed perspiciatis.</p>
  <span class="btn">Learn More</span>
  <div class="about-art" role="img" aria-label="Illustration of a team analysing search results with a magnifying glass"></div>
</section>

<section class="testimonials">
  <h2 class="section-title" style="margin-top:70px">Our Testimonials</h2>
  <div class="rule"></div>
  <p class="section-sub">Read what our clients say about working with us on their link building.</p>
  <div class="quotes">
    <div class="quote"><div class="avatar" role="img" aria-label="Client portrait"></div>
      <p>Sed ut perspiciatis unde omnis iste natus error sit voluptatem accusantium doloremque laudantium totam rem.</p>
      <h4>Marlon Keswick</h4><span>Company Name</span></div>
    <div class="quote mid"><div class="avatar" role="img" aria-label="Client portrait"></div>
      <p>Sed ut perspiciatis unde omnis iste natus error sit voluptatem accusantium doloremque laudantium totam rem.</p>
      <h4>Tessa Orrin</h4><span>Company Name</span></div>
    <div class="quote"><div class="avatar" role="img" aria-label="Client portrait"></div>
      <p>Sed ut perspiciatis unde omnis iste natus error sit voluptatem accusantium doloremque laudantium totam rem.</p>
      <h4>Colin Ravel</h4><span>Company Name</span></div>
  </div>
  <div class="dots"><i></i><i></i><i></i></div>
</section>

<section class="faq">
  <h2 class="section-title">Frequently Asked Questions</h2>
  <div class="rule"></div>
  <p class="section-sub">Quick answers to common questions.</p>
  <div class="faq-list">
    <div class="faq-item">How to work with us?</div>
    <div class="faq-item open">How long it takes to see results?</div>
    <div class="faq-answer">Lorem ipsum dolor sit amet, consectetur adipiscing elit, sed do eiusmod tempor incididunt ut labore et dolore magna aliqua. Ut enim ad minim veniam, quis nostrud exercitation ullamco laboris nisi ut aliquip ex ea commodo consequat.</div>
    <div class="faq-item">How does it works?</div>
    <div class="faq-item">How to get a monthly subscription?</div>
    <div class="faq-item">How to get premium links?</div>
  </div>
  <span class="btn">More Questions</span>
</section>

<section class="contact">
  <div class="contact-card">
    <div class="form">
      <h2>Contact Us</h2><div class="rule"></div>
      <div class="row"><div class="field">Your Name</div><div class="field">Your Email</div></div>
      <div class="row"><div class="field">Your Subject</div><div class="field">Phone Number</div></div>
      <div class="row"><div class="field area">Your Message</div></div>
      <span class="btn">Submit ➜</span>
    </div>
    <div class="info">
      <div class="info-item"><div class="info-icon"><svg width="18" height="18" viewBox="0 0 24 24" fill="none" stroke="var(--orange)" stroke-width="2"><rect x="3" y="5" width="18" height="14" rx="1"/><path d="M3 6l9 7 9-7"/></svg></div>
        <div><h4>Email</h4><p>hello@northpeak-mail.com</p></div></div>
      <div class="info-item"><div class="info-icon"><svg width="18" height="18" viewBox="0 0 24 24" fill="none" stroke="var(--orange)" stroke-width="2"><rect x="7" y="2" width="10" height="20" rx="2"/><path d="M11 18h2"/></svg></div>
        <div><h4>Phone Number</h4><p>(555) 014 2287</p></div></div>
      <div class="info-item"><div class="info-icon"><svg width="18" height="18" viewBox="0 0 24 24" fill="none" stroke="var(--orange)" stroke-width="2"><path d="M12 22s7-7 7-12a7 7 0 0 0-14 0c0 5 7 12 7 12z"/><circle cx="12" cy="10" r="2.5"/></svg></div>
        <div><h4>Visit our office</h4><p>Street Adress, City,<br>State, Country</p></div></div>
    </div>
  </div>
</section>

<footer class="site-footer">
  <div class="footer-mark" aria-hidden="true">Northpeak</div>
  <div class="footer-cols">
    <div class="col-about">
      <h4>About Your Company</h4>
      <p>Lorem ipsum dolor sit amet, consectetur adipiscing elit, sed do eiusmod tempor incididunt ut labore et dolore magna aliqua. Ut enim ad minim veniam, quis nostrud exercitation.</p>
      <p class="call">Give us a Call</p>
      <p class="phone">(555) 014 2287</p>
    </div>
    <div class="col-links">
      <h4>Quick Links</h4>
      <div class="links">
        <span>Services</span><span>Privacy Policy</span>
        <span class="current">About Us</span><span>Terms &amp; Conditions</span>
        <span>Testimonials</span><span></span>
        <span>Faq</span><span></span>
        <span>Contact Us</span>
      </div>
    </div>
    <div class="news">
      <h4>Newsletter</h4>
      <div class="input">Enter your email</div>
      <span class="btn">Subscribe ✉</span>
    </div>
  </div>
  <div class="footer-bottom">
    <span>Copyright © Northpeak 2024 All Rights Reserved.</span>
    <div class="socials"><i></i><i></i><i></i><i></i></div>
  </div>
</footer>

</body>
</html>
```